Tessmar Fahrwerkstatt
Sehr angenehme zusammenarbeit nicht aufdringlich und genau auf die Wünsche eingegangen. Wir werde sicher noch mehr zusammen Arbeiten. Gruss Lukas Hegemann Inhaber Tessmar Fahrwerkstatt
Zielgruppe
Dinks und Kunden mit viel Erfolg und hohem Ausgabepotential.
Aufgabenstellung
Unsere Firma vertreibt Fahrzeuge im Luxusbereich hauptgebiet Valmerra aber auch andere Sportwagen. Was uns fehlt ist ein optischer Wiedererkennugswert. Deshalb hätten wir gerne ein Visitenkarten Design und Briefpapier Design. Später soll auch noch eine Webseite mit gleichem Wiedererkennungswert entstehen. " Roter Faden "

```html
<!DOCTYPE html>
<html lang="de">
<head>
<meta charset="utf-8">
<title>Tessmar Fahrwerkstatt – Visitenkarte</title>
<link rel="stylesheet" href="https://fonts.googleapis.com/css2?family=Alegreya:wght@400;700&display=swap">
<style>
  :root {
    --steel: #5b7898;
    --steel-light: #7a93b0;
    --ink: #1c1c1c;
    --paper: #ffffff;
    --stage: #f4f5f7;
  }
  * { margin: 0; padding: 0; box-sizing: border-box; }
  html, body {
    width: 1200px;
    height: 845px;
    overflow: hidden;
    background: var(--stage);
    font-family: "Alegreya", Georgia, serif;
  }
  .sheet {
    position: relative;
    width: 1200px;
    height: 845px;
  }
  .card {
    position: absolute;
    top: 266px;
    width: 485px;
    height: 314px;
  }
  .card--front {
    left: 90px;
    background: var(--paper);
    border: 1px solid #e2e5ea;
  }
  .card--back {
    left: 625px;
    background: var(--steel);
  }

  /* Wordmark */
  .wordmark {
    position: absolute;
    left: 29px;
    top: 30px;
    display: flex;
    align-items: center;
    gap: 20px;
  }
  .wordmark__square {
    width: 44px;
    height: 44px;
    border-radius: 6px;
    background: var(--steel);
  }
  .wordmark__name {
    font-size: 22px;
    line-height: 1.05;
    letter-spacing: 3px;
    color: var(--ink);
    font-weight: 400;
  }

  /* Contact block */
  .contact {
    position: absolute;
    left: 95px;
    top: 128px;
    font-size: 12.5px;
    line-height: 1.2;
    letter-spacing: 1.6px;
    color: var(--ink);
  }
  .contact__group { margin-bottom: 13px; }
  .contact__label {
    color: var(--steel-light);
    font-weight: 700;
  }

  /* Back side */
  .back-mark {
    position: absolute;
    right: 36px;
    bottom: 30px;
    display: flex;
    align-items: center;
    gap: 18px;
  }
  .back-mark__name {
    font-size: 22px;
    line-height: 1.05;
    letter-spacing: 3px;
    color: var(--paper);
    text-align: right;
  }
  .back-mark__square {
    width: 115px;
    height: 115px;
    border-radius: 16px;
    background: var(--paper);
  }
</style>
</head>
<body>
<main class="sheet">
  <section class="card card--front" aria-label="Visitenkarte Vorderseite">
    <div class="wordmark">
      <span class="wordmark__square" aria-hidden="true"></span>
      <span class="wordmark__name">tessmar<br>fahrwerkstatt</span>
    </div>
    <div class="contact">
      <div class="contact__group">
        <div class="contact__label">Lukas Hegemann</div>
        <div>+41795128436</div>
      </div>
      <div class="contact__group">
        <div>info@tessmar.ch</div>
        <div>www.tessmar.ch</div>
      </div>
      <div class="contact__group">
        <div class="contact__label">Büro</div>
        <div>Lindenweg 12 - CH 8173 Neerach</div>
      </div>
      <div class="contact__group">
        <div class="contact__label">Showroom</div>
        <div>Seefeldstrasse 9 - CH 8604 Hegnau</div>
      </div>
    </div>
  </section>

  <section class="card card--back" aria-label="Visitenkarte Rückseite">
    <div class="back-mark">
      <span class="back-mark__name">tessmar<br>fahrwerkstatt</span>
      <span class="back-mark__square" aria-hidden="true"></span>
    </div>
  </section>
</main>
</body>
</html>
```